Simple and Clean business card design

We would like the design to be simple clean and to incorporate our colors.

We are open to your design and talent, we have the dots in our logo as we think of it as data points and we connect data points for people.

We are open to see the great creative and clean design you bring to the table

Contact Information for Business Card

please include: name, position, email, phone and website

Font styles to use
Sans Serif

Requirements
Must have
• my colors incorporated, simplicity
Nice to have
• lots of white space, simplicity
Should not have
• complexicity/ complex art

```html
<!DOCTYPE html>
<html lang="en">
<head>
<meta charset="utf-8">
<title>Tessel — Business Card</title>
<link href="https://fonts.googleapis.com/css2?family=Montserrat:wght@400;500;600;700&display=swap" rel="stylesheet">
<style>
  :root {
    --stage: #26262b;
    --paper: #ffffff;
    --ink: #0a0a0a;
    --night: #000000;
    --blue: #5a7fc6;
    --text-soft: #1c1c1c;
  }
  * { box-sizing: border-box; margin: 0; padding: 0; }
  html, body { width: 1200px; height: 786px; overflow: hidden; }
  body {
    background: var(--stage);
    font-family: "Montserrat", sans-serif;
    position: relative;
  }
  .card {
    position: absolute;
    top: 243px;
    width: 520px;
    height: 300px;
    overflow: hidden;
    border: 6px solid var(--blue);
  }
  .card--front { left: 50px; background: var(--paper); }
  .card--back { left: 630px; background: var(--night); }

  .brand {
    position: absolute;
    display: flex;
    align-items: center;
    gap: 10px;
    font-weight: 700;
    letter-spacing: -1px;
    line-height: 1;
  }
  .brand__dot { border-radius: 50%; background: var(--blue); flex: none; }
  .card--front .brand { left: 40px; top: 124px; font-size: 54px; color: var(--ink); }
  .card--front .brand__dot { width: 14px; height: 14px; }
  .card--back .brand { left: 0; right: 0; top: 112px; justify-content: center; font-size: 72px; color: #ffffff; }
  .card--back .brand__dot { width: 18px; height: 18px; }

  .divider {
    position: absolute;
    left: 262px; top: 64px;
    width: 1px; height: 160px;
    background: var(--blue);
  }
  .contact {
    position: absolute;
    left: 280px; top: 64px;
    color: var(--text-soft);
    font-size: 11px;
    line-height: 1.45;
  }
  .contact__name {
    color: var(--blue);
    font-weight: 600;
    font-size: 17px;
    letter-spacing: 1px;
    text-transform: uppercase;
    line-height: 1.1;
  }
  .contact__role { font-size: 11.5px; margin-bottom: 10px; }
  .contact__address { margin-bottom: 10px; }
  .contact__row { display: flex; align-items: center; gap: 6px; }
  .contact__icon { width: 9px; height: 9px; flex: none; }
</style>
</head>
<body>

  <section class="card card--front" aria-label="Business card front">
    <div class="brand"><span class="brand__dot"></span>Tessel</div>

    <div class="divider"></div>

    <div class="contact">
      <p class="contact__name">Dana Whitford</p>
      <p class="contact__role">Founder</p>
      <p class="contact__address">418 Corbin Lane<br>Marlow, TX 78021</p>
      <p class="contact__row">
        <svg class="contact__icon" viewBox="0 0 10 10" aria-hidden="true"><path d="M2 1 L4 3 L3 4 Q4 6 6 7 L7 6 L9 8 L8 9 Q2 9 1 2 Z" fill="var(--blue)"/></svg>
        0412 386 209
      </p>
      <p class="contact__row">
        <svg class="contact__icon" viewBox="0 0 10 10" aria-hidden="true"><rect x="0.5" y="2" width="9" height="6" fill="none" stroke="var(--blue)"/><path d="M0.5 2 L5 5.5 L9.5 2" fill="none" stroke="var(--blue)"/></svg>
        hello@tesseldata.com
      </p>
      <p class="contact__row">
        <svg class="contact__icon" viewBox="0 0 10 10" aria-hidden="true"><circle cx="5" cy="5" r="4.3" fill="none" stroke="var(--blue)"/><ellipse cx="5" cy="5" rx="1.8" ry="4.3" fill="none" stroke="var(--blue)"/><line x1="0.7" y1="5" x2="9.3" y2="5" stroke="var(--blue)"/></svg>
        www.tesseldata.com
      </p>
    </div>
  </section>

  <section class="card card--back" aria-label="Business card back">
    <div class="brand"><span class="brand__dot"></span>Tessel</div>
  </section>

</body>
</html>
```